Dental Savings Plan - Raymond Castell DDS

We need a tri-fold brochure and 1 page flyer/poster for Dr. Raymond Castell' dental office located on Maui, Hawaii. We are offering a new "Dental Savings Plan" to patients.
I have included 3 photos, along with the office logo. You do not have to use all photos if you do not want to. We want this to catch the eyes of patients, easy for them to read and understand, and to show them that this is a much better option than dental insurance.
Please use same Hawaiian theme and colors on the office website https://www.brightcoveclinic.com .

Please also include the following to promote this new plan:

Dental Services Include
• Professional Dental Cleanings (2 per benefit year)
• Perio Maintenance Cleanings (3 per benefit year) covered at 80%
• Radiographs as needed (1 set of X-rays per benefit year)
• Doctor Examinations (2 per benefit year)
• Ozone Treatment
• BRISK Amalgam Removal
• Additional limited/emergency exam (1 per benefit year)
• Cosmetic consultation
• 15% discount on all other services (including cosmetic procedures)
• 10% discount on implants and implant crowns

Advantages of the Dental Savings Plan
1. No deductibles
2. No waiting periods
3. No claims to file
4. No frequency limitations or exclusions
5. No yearly maximum benefits
6. No pre-authorization requirements
7. No pre-existing conditions limitations
8. State of the art facility and technology
9. Immediate enrollment
10. Highest quality of care for you and your Ohana

Annual Fee
$399 first family member/individual (equivalent to $33 per month)
$349 second family member (equivalent to $29 per month)
$249 each additional family member (equivalent to $20 per month)

Provisions of the Dental Savings Plan
• May not be combined with insurance plans, discounts or promotions
• This Dental Savings Plan is not an insurance plan, but a payment arrangement provided by Raymond Castell DDS, and is not transferable to any other dental office or dental specialist
• Payment for services are due at the date of service
• This program is for you and is not transferable
• Benefits are provided for one year from the date the plan is purchased
• Must be paid in full when starting the plan
• No refunds will be provided for dues of the plan annual fee under any circumstances, including failure to schedule and maintain appointments
• If Pay Ladder is used to pay for the program and for services then only a 10% discount will be given
• To receive the full 15% discount on restorative treatment, you must schedule the appointment the day it is recommended. Any failed appointment results in the loss of the 15% discount.

Target Market(s)

Dental patients without dental insurance

Industry/Entity Type

Dental Clinic

Requirements
Must have
• My project must have the logo file to identify the dental office, Hawaiian theme, same colors as website, match style of website font, theme and colors, as well as, all the Dental Services, Advantages of the Dental Savings Plan, Annual Fee, and the Provisions of the Dental Savings Plan.

```html
<!DOCTYPE html>
<html lang="en">
<head>
<meta charset="utf-8">
<title>Dental Savings Plan Brochure – Raymond Castell DDS</title>
<link href="https://fonts.googleapis.com/css2?family=Exo+2:ital,wght@0,600;1,600;1,700&family=Roboto+Condensed:wght@400;700&display=swap" rel="stylesheet">
<style>
:root{
  --blue:#29abe2;
  --blue-deep:#1b8fc4;
  --charcoal:#3a3b3e;
  --green:#7ac143;
  --ink:#333;
  --paper:#ffffff;
  --panel-grey:#f1f1f1;
  --stage:#dcdcdc;
}
*{margin:0;padding:0;box-sizing:border-box}
html,body{width:1200px;height:923px;overflow:hidden}
body{background:linear-gradient(#cfcfcf,#eeeeee);font-family:"Roboto Condensed",sans-serif;color:var(--ink);position:relative}
.sheet{position:absolute;overflow:hidden;box-shadow:0 6px 18px rgba(0,0,0,.18)}
.sheet svg.bg{position:absolute;inset:0}
.sheet-outside{left:24px;top:30px;width:520px;height:402px;background:var(--blue)}
.sheet-inside{left:560px;top:420px;width:616px;height:476px;background:var(--panel-grey)}
.abs{position:absolute}

/* outside */
.fee-title{left:30px;top:44px;font:700 italic 22px "Exo 2",sans-serif;color:var(--charcoal)}
.fee-list{left:26px;top:80px;width:132px;list-style:none}
.fee-list li{font-size:9px;line-height:1.15;margin-bottom:12px;color:var(--ink)}
.fee-list .price{font:700 italic 13px "Exo 2",sans-serif}
.fee-list .blue{color:var(--blue)}
.fee-list .dark{color:var(--charcoal)}
.fee-list .eq{display:block;font-size:8.5px}
.offer-box{left:190px;top:250px;width:140px;padding:10px 8px;background:rgba(40,58,66,.88);border-radius:8px;text-align:center;color:#fff;font:600 13px/1.25 "Exo 2",sans-serif}
.offer-box em{color:var(--green);font-style:italic;font-weight:700}
.brand{left:360px;top:96px;width:150px;text-align:center}
.brand-dot{width:22px;height:22px;border-radius:50%;background:var(--green);margin:0 auto 6px}
.brand-name{font:600 13px "Exo 2",sans-serif;color:var(--green);letter-spacing:.5px}
.brand-tag{font:600 italic 10px "Exo 2",sans-serif;color:var(--blue);margin-top:3px}
.contact{left:366px;top:300px;list-style:none}
.contact li{display:flex;align-items:center;gap:6px;font-size:9.5px;color:var(--charcoal);margin-bottom:6px}
.contact svg{flex:none}

/* inside */
.panel{position:absolute;top:0;width:205px;height:440px}
.panel-1{left:0}.panel-2{left:205px}.panel-3{left:410px}
.icon-disc{position:absolute;width:58px;height:58px;border-radius:50%;background:var(--blue);border:3px solid #fff}
.panel h2{position:absolute;font:600 italic 15px/1.15 "Exo 2",sans-serif;color:var(--blue)}
.bullets{position:absolute;list-style:none}
.bullets li{font-size:8.3px;line-height:1.2;padding-left:8px;position:relative;margin-bottom:8.5px}
.bullets li::before{content:"•";position:absolute;left:0}
.numbers{position:absolute;list-style:none}
.numbers li{font-size:8.6px;margin-bottom:13.3px;padding-left:14px;position:relative}
.numbers li span{position:absolute;left:0}
.provisions li{font-size:7.6px;margin-bottom:9px}
</style>
</head>
<body>

<!-- Outside of the tri-fold -->
<section class="sheet sheet-outside" aria-label="Brochure outside">
  <svg class="bg" width="520" height="402" viewBox="0 0 520 402">
    <defs>
      <linearGradient id="beach" x1="0" y1="0" x2="0" y2="1">
        <stop offset="0" stop-color="#3f8fd8"/>
        <stop offset=".45" stop-color="#bfe0f5"/>
        <stop offset=".6" stop-color="#2fb3c9"/>
        <stop offset="1" stop-color="#0f7f93"/>
      </linearGradient>
      <linearGradient id="clinic" x1="0" y1="0" x2="1" y2="1">
        <stop offset="0" stop-color="#f3d9c8"/>
        <stop offset=".6" stop-color="#e9e9ec"/>
        <stop offset="1" stop-color="#cfd3d8"/>
      </linearGradient>
    </defs>
    <!-- left panel -->
    <polygon points="10,40 120,14 163,14 163,205 10,205" fill="var(--paper)"/>
    <polygon points="10,40 90,20 10,20" fill="var(--charcoal)"/>
    <circle cx="60" cy="22" r="12" fill="var(--blue)" stroke="#fff" stroke-width="2"/>
    <rect x="0" y="205" width="173" height="197" fill="url(#clinic)" role="img" aria-label="Photo of a smiling patient at a dental check-up"/>
    <!-- middle panel -->
    <rect x="173" y="40" width="174" height="335" fill="url(#beach)" role="img" aria-label="Photo of a palm tree over a turquoise Maui beach"/>
    <polygon points="173,40 260,25 347,40" fill="var(--charcoal)"/>
    <polygon points="173,375 347,360 347,375" fill="var(--charcoal)"/>
    <!-- right panel -->
    <polygon points="347,0 520,0 520,190 440,175 347,200" fill="var(--charcoal)"/>
    <polygon points="347,200 440,175 520,190 520,225 347,265" fill="var(--blue)"/>
    <polygon points="347,265 520,225 520,402 347,402" fill="var(--paper)"/>
  </svg>

  <h2 class="abs fee-title">Annual Fee</h2>
  <ul class="abs fee-list">
    <li><span class="price blue">$399</span> <span class="blue">first family member/individual</span><span class="eq">(equivalent to $33 per month)</span></li>
    <li><span class="price dark">$349</span> second family member<span class="eq">(equivalent to $29 per month)</span></li>
    <li><span class="price blue">$249</span> <span class="blue">each additional family member</span><span class="eq">(equivalent to $20 per month)</span></li>
  </ul>

  <p class="abs offer-box">We are offering<br>a new<br><em>“Dental Savings Plan”</em><br>to patients</p>

  <div class="abs brand">
    <div class="brand-dot"></div>
    <div class="brand-name">RAYMOND CASTELL DDS</div>
    <div class="brand-tag">Bright Cove Smiles</div>
  </div>

  <ul class="abs contact">
    <li><svg width="12" height="12" viewBox="0 0 12 12"><circle cx="6" cy="6" r="5.3" fill="none" stroke="var(--charcoal)"/><path d="M4 3.5l1 1.5-.6.7a4 4 0 0 0 2 2l.7-.6 1.5 1-.7 1C5.5 9 3 6.5 3 4.2z" fill="var(--charcoal)"/></svg>808-555-0172</li>
    <li><svg width="12" height="12" viewBox="0 0 12 12"><circle cx="6" cy="6" r="5.3" fill="none" stroke="var(--charcoal)"/><rect x="3" y="4" width="6" height="4" fill="none" stroke="var(--charcoal)" stroke-width=".8"/><path d="M3 4l3 2.2L9 4" fill="none" stroke="var(--charcoal)" stroke-width=".8"/></svg>hello@brightcoveclinic.com</li>
    <li><svg width="12" height="12" viewBox="0 0 12 12"><circle cx="6" cy="6" r="5.3" fill="none" stroke="var(--charcoal)"/><circle cx="6" cy="6" r="3" fill="none" stroke="var(--charcoal)" stroke-width=".8"/><path d="M3 6h6M6 3v6" stroke="var(--charcoal)" stroke-width=".8"/></svg>www.brightcoveclinic.com</li>
    <li><svg width="12" height="12" viewBox="0 0 12 12"><circle cx="6" cy="6" r="5.3" fill="none" stroke="var(--charcoal)"/><path d="M6 9.5S3.8 6.8 3.8 5.2a2.2 2.2 0 0 1 4.4 0C8.2 6.8 6 9.5 6 9.5z" fill="var(--charcoal)"/></svg>742 Palm Shore Ave # 12, Kihei, HI 96753</li>
    <li><svg width="20" height="20" viewBox="0 0 20 20"><rect x="1" y="1" width="18" height="18" fill="none" stroke="var(--charcoal)" stroke-width="1.4"/><path d="M10 16s-4-4.5-4-7.3a4 4 0 0 1 8 0C14 11.5 10 16 10 16z" fill="none" stroke="var(--charcoal)" stroke-width="1.4"/><circle cx="10" cy="8.6" r="1.4" fill="var(--charcoal)"/></svg></li>
  </ul>
</section>

<!-- Inside of the tri-fold -->
<section class="sheet sheet-inside" aria-label="Brochure inside">
  <svg class="bg" width="616" height="476" viewBox="0 0 616 476">
    <rect x="0" y="0" width="205" height="440" fill="var(--paper)"/>
    <rect x="410" y="0" width="206" height="440" fill="var(--paper)"/>
    <polygon points="0,0 616,0 616,10 420,14 250,90 205,70 40,30 0,150" fill="var(--blue)"/>
    <polygon points="0,150 40,30 60,34 0,175" fill="var(--charcoal)"/>
    <polygon points="250,90 420,14 616,10 616,18 430,18" fill="var(--charcoal)"/>
    <rect x="0" y="440" width="616" height="36" fill="var(--charcoal)"/>
    <polygon points="0,440 120,440 0,462" fill="var(--blue)"/>
    <polygon points="520,440 616,420 616,440" fill="var(--charcoal)"/>
    <line x1="205" y1="0" x2="205" y2="440" stroke="#e3e3e3"/>
    <line x1="410" y1="0" x2="410" y2="440" stroke="#e3e3e3"/>
  </svg>

  <div class="panel panel-1">
    <div class="icon-disc" style="left:40px;top:34px" role="img" aria-label="Dental chair icon"></div>
    <h2 style="left:18px;top:128px">Dental Services Include</h2>
    <ul class="bullets" style="left:18px;top:158px;width:182px">
      <li>Professional Dental Cleanings<br>(2 per benefit year)</li>
      <li>Perio Maintenance Cleanings<br>(3 per benefit year) covered at 80%</li>
      <li>Radiographs as needed<br>(1 set of X-rays per benefit year)</li>
      <li>Doctor Examinations<br>(2 per benefit year)</li>
      <li>Ozone Treatment</li>
      <li>BRISK Amalgam Removal</li>
      <li>Additional limited/emergency exam<br>(1 per benefit year)</li>
      <li>Cosmetic consultation</li>
      <li>15% discount on all other services<br>(including cosmetic procedures)</li>
      <li>10% discount on implants and implant crowns</li>
    </ul>
  </div>

  <div class="panel panel-2">
    <div class="icon-disc" style="left:70px;top:40px" role="img" aria-label="Tooth icon"></div>
    <h2 style="left:12px;top:126px">Advantages of the<br>Dental Savings Plan</h2>
    <ol class="numbers" style="left:12px;top:176px;width:190px">
      <li><span>1.</span>No deductibles</li>
      <li><span>2.</span>No waiting periods</li>
      <li><span>3.</span>No claims to file</li>
      <li><span>4.</span>No frequency limitations or exclusions</li>
      <li><span>5.</span>No yearly maximum benefits</li>
      <li><span>6.</span>No pre-authorization requirements</li>
      <li><span>7.</span>No pre-existing conditions limitations</li>
      <li><span>8.</span>State of the art facility and technology</li>
      <li><span>9.</span>Immediate enrollment</li>
      <li><span>10.</span>Highest quality of care for you<br>and your Ohana</li>
    </ol>
  </div>

  <div class="panel panel-3">
    <h2 style="left:10px;top:40px">Provisions<br>of the Dental<br>Savings Plan</h2>
    <div class="icon-disc" style="left:134px;top:28px" role="img" aria-label="Tooth with magnifier icon"></div>
    <ul class="bullets provisions" style="left:10px;top:112px;width:186px">
      <li>May not be combined with insurance plans, discounts or promotions</li>
      <li>This Dental Savings Plan is not an insurance plan, but a payment arrangement provided by Raymond Castell DDS, and is not transferable to any other dental office or dental specialist</li>
      <li>Payment for services are due at the date of service</li>
      <li>This program is for you and is not transferable</li>
      <li>Benefits are provided for one year from the date the plan is purchased</li>
      <li>Must be paid in full when starting the plan</li>
      <li>No refunds will be provided for dues of the plan annual fee under any circumstances, including failure to schedule and maintain appointments</li>
      <li>If Pay Ladder is used to pay for the program and for services then only a 10% discount will be given</li>
      <li>To receive the full 15% discount on restorative treatment, you must schedule the appointment the day it is recommended. Any failed appointment results in the loss of the 15% discount.</li>
    </ul>
  </div>
</section>

</body>
</html>
```